Designer Instructions – Updated Referral Program Flyer

(Based on the mock-up in “Brief Layout and Instructions.pdf”)

OVERALL STYLE + LAYOUT

Maintain the same general layout, structure, and flow as the mock-up flyer (front and back).

This is an update of an older flyer, not a full redesign — keep the same sections, proportions, and overall visual feel, but with cleaner, more modern design improvements.

The final flyer should look clean, bold, professional, and high-impact, geared toward realtors, property managers, and contractors who refer work.

FRONT SIDE INSTRUCTIONS
1. Header Section

Remove the Rebuild Harbor Crest logo from the top banner.
(Shown on page 1 of the PDF)

2. Main Headline

Keep the same three-line structure:
EARN
UNLIMITED
CASH

Center it, maximize impact, and increase the font size of CASH so all three words match in importance.

Make the headline bold, clean, and the main focal point.

3. Cash Incentive Box

Keep the "$500 minimum OR 10% per referral" box, but upgrade the graphics to look sharper and more modern.

Ensure the wording matches exactly what’s in the mock-up.

4. Premier Partner Program Ribbon

Clean up and modernize the "PREMIER PARTNER PROGRAM" bar while keeping the same position and structure.

Ensure the checkmark badge remains crisp and professional.

5. Supporting Icons Section

Keep the four icons/benefit boxes (Guaranteed Payout, Free Evaluations, Affordable Solutions, Industry Leaders) in the same order.

Update the icons to cleaner, more modern styles — but maintain the same meanings.

Improve alignment and spacing for sharper visual consistency.

6. Remove Icons in Contact Area

At the bottom (“CALL TEXT OR BOOK ONLINE 858-471-6093 BrightlaneRenovate.com”), remove the phone and internet icons, as noted on page 2 of the PDF.

7. Replace All Images

I (Dorian) will provide all updated stock images separately via email.

Replace the flood/water-damage imagery and roof leak with the new images I send.

Keep image placement and proportions the same as the mock-up.

BACK SIDE INSTRUCTIONS
1. Header Image + “REFER / EARN” Section

Maintain the same large split-image layout (“The more you refer, the more you earn”).

Replace all background imagery with the new assets I will send.

Keep the CASH FLOW image section but modernize the type and spacing.

2. “HOW IT WORKS” Section

Preserve the three-column layout:

Refer Flood, Water & Mold Damage

We Take Care of Everything (evaluations/insurance)

Get Paid to Share

Update images, tighten spacing, and use modern iconography.

3. Remove Phone/Internet Icons

Same as the front side — remove small communication icons and keep only the text/number/URL.

4. Bottom Contact Bar

Keep the blue bar, same wording, same layout — just modernize the style if needed for clarity.

5. Replace All Back-Side Images

Again, I will email you the image assets.

Keep the layout EXACT — just update with higher-quality photos and improved design.

TEXT CONTENT (Keep as-is unless spacing adjustments needed)

All text shown in the PDF should remain exactly the same unless spacing or visual balance requires minor adjustments.
Example from page 3:

“REFER FLOOD, MOLD & CONSTRUCTION JOBS”

“We Schedule a Free Estimate. If Approved, You Get Paid.”

“Everybody Benefits From Referrals”

Everything stays, just refreshed and visually improved.

DESIGN GOALS

Flyer should look high-end and trustworthy, not salesy.

Consistent color theme: blues, whites, yellows, same palette as original.

Use bold, modern fonts with strong readability.

Ensure all headlines pop and all benefit boxes are clean, well-aligned, and evenly spaced.

The final result should feel like a premium referral program flyer for a top-tier restoration/remodel company.

FILES I WILL PROVIDE

I will send the designer:

All replacement stock photos

Any updated logos (if needed)

Original high-resolution version of the mock-up (if available)

Any additional icons preferred

Colors
0054AA
0677BA
7BADD7
CADEEF
E8F1F8

Requirements
Must have
• Designer Instructions – Updated Referral Program Flyer (Based on the mock-up in “Brief Layout and Instructions.pdf”) OVERALL STYLE + LAYOUT Maintain the same general layout, structure, and flow as the mock-up flyer (front and back). This is an update of an older flyer, not a full redesign — keep the same sections, proportions, and overall visual feel, but with cleaner, more modern design improvements. The final flyer should look clean, bold, professional, and high-impact, geared toward realtors, property managers, and contractors who refer work. FRONT SIDE INSTRUCTIONS 1. Header Section Remove the Rebuild Harbor Crest logo from the top banner. (Shown on page 1 of the PDF) 2. Main Headline Keep the same three-line structure: EARN UNLIMITED CASH Center it, maximize impact, and increase the font size of CASH so all three words match in importance. Make the headline bold, clean, and the main focal point. 3. Cash Incentive Box Keep the "$500 minimum OR 10% per referral" box, but upgrade the graphics to look sharper and more modern. Ensure the wording matches exactly what’s in the mock-up. 4. Premier Partner Program Ribbon Clean up and modernize the "PREMIER PARTNER PROGRAM" bar while keeping the same position and structure. Ensure the checkmark badge remains crisp and professional. 5. Supporting Icons Section Keep the four icons/benefit boxes (Guaranteed Payout, Free Evaluations, Affordable Solutions, Industry Leaders) in the same order. Update the icons to cleaner, more modern styles — but maintain the same meanings. Improve alignment and spacing for sharper visual consistency. 6. Remove Icons in Contact Area At the bottom (“CALL TEXT OR BOOK ONLINE 858-471-6093 BrightlaneRenovate.com”), remove the phone and internet icons, as noted on page 2 of the PDF. 7. Replace All Images I (Dorian) will provide all updated stock images separately via email. Replace the flood/water-damage imagery and roof leak with the new images I send. Keep image placement and proportions the same as the mock-up. BACK SIDE INSTRUCTIONS 1. Header Image + “REFER / EARN” Section Maintain the same large split-image layout (“The more you refer, the more you earn”). Replace all background imagery with the new assets I will send. Keep the CASH FLOW image section but modernize the type and spacing. 2. “HOW IT WORKS” Section Preserve the three-column layout: Refer Flood, Water & Mold Damage We Take Care of Everything (evaluations/insurance) Get Paid to Share Update images, tighten spacing, and use modern iconography. 3. Remove Phone/Internet Icons Same as the front side — remove small communication icons and keep only the text/number/URL. 4. Bottom Contact Bar Keep the blue bar, same wording, same layout — just modernize the style if needed for clarity. 5. Replace All Back-Side Images Again, I will email you the image assets. Keep the layout EXACT — just update with higher-quality photos and improved design. TEXT CONTENT (Keep as-is unless spacing adjustments needed) All text shown in the PDF should remain exactly the same unless spacing or visual balance requires minor adjustments. Example from page 3: “REFER FLOOD, MOLD & CONSTRUCTION JOBS” “We Schedule a Free Estimate. If Approved, You Get Paid.” “Everybody Benefits From Referrals” Everything stays, just refreshed and visually improved. DESIGN GOALS Flyer should look high-end and trustworthy, not salesy. Consistent color theme: blues, whites, yellows, same palette as original. Use bold, modern fonts with strong readability. Ensure all headlines pop and all benefit boxes are clean, well-aligned, and evenly spaced. The final result should feel like a premium referral program flyer for a top-tier restoration/remodel company. FILES I WILL PROVIDE I will send the designer: All replacement stock photos Any updated logos (if needed) Original high-resolution version of the mock-up (if available) Any additional icons preferred

```html
<!DOCTYPE html>
<html lang="en">
<head>
<meta charset="utf-8">
<title>Referral Program Flyer – Front and Back</title>
<link rel="stylesheet" href="https://fonts.googleapis.com/css2?family=Anton&family=Poppins:wght@400;500;600;700;800;900&family=Roboto+Condensed:wght@300;400&display=swap">
<style>
  :root{
    --navy:#1d4a78;
    --navy-deep:#0c2136;
    --blue:#22609a;
    --blue-bright:#1f66ad;
    --red:#d1393f;
    --yellow:#f0cf2c;
    --orange:#f0a33a;
    --mist:#e3e5ea;
    --white:#ffffff;
    --page:#d5d7db;
  }
  *{margin:0;padding:0;box-sizing:border-box}
  html,body{width:936px;height:1200px;overflow:hidden;background:var(--page)}
  body{position:relative;font-family:"Poppins",sans-serif;color:var(--navy)}
  .card{position:absolute;left:122px;width:684px;height:442px;background:var(--white);overflow:hidden}
  .card--front{top:104px}
  .card--back{top:601px}
  .card svg.shapes{position:absolute;left:0;top:0;width:684px;height:442px}
  .abs{position:absolute}

  /* Front headline */
  .headline{position:absolute;left:0;top:24px;width:284px;text-align:center;font-weight:900;line-height:1}
  .headline span{display:block}
  .headline .earn{color:var(--yellow);font-size:58px;letter-spacing:1px}
  .headline .unlimited{color:var(--white);font-size:41px;margin-top:8px}
  .headline .cash{color:var(--yellow);font-size:60px;margin-top:6px;letter-spacing:1px}

  /* Incentive */
  .amount{color:var(--white);font-weight:800;line-height:1;text-align:center}
  .amount .big{font-size:40px;display:block;letter-spacing:-1px}
  .amount .big sup{font-size:20px;vertical-align:top;position:relative;top:2px}
  .amount .small{font-size:14px;font-weight:700;display:block;margin-top:3px}
  .amount--min{left:50px;top:236px;width:100px}
  .amount--pct{left:222px;top:236px;width:116px}
  .or-box{left:161px;top:243px;width:50px;height:34px;background:var(--yellow);color:var(--navy);font-weight:800;font-size:22px;line-height:34px;text-align:center}

  .ribbon-text{font-weight:800;line-height:1;color:var(--white);font-size:15px;text-align:center}
  .ribbon-premier{left:400px;top:233px;width:200px;color:var(--navy);font-size:17px}
  .ribbon-partner{left:370px;top:267px;width:100px}
  .ribbon-program{left:530px;top:267px;width:100px}

  /* Benefits */
  .benefits{position:absolute;left:0;top:300px;width:684px;height:104px;background:var(--mist)}
  .spaced{font-weight:700;letter-spacing:3.2px;text-align:center;font-size:12px;width:684px;left:0}
  .spaced .r{color:var(--red)} .spaced .n{color:var(--navy)}
  .benefits-title{top:5px}
  .benefits-footer{top:86px}
  .benefit{position:absolute;top:23px}
  .benefit h3{font-size:12.5px;font-weight:500;line-height:14px;color:var(--navy);text-transform:uppercase}
  .benefit p{font-size:9.6px;font-weight:600;line-height:12.5px;color:var(--navy);margin-top:4px;white-space:nowrap}
  .benefit .icon{position:absolute;top:-2px;width:24px;height:26px}
  .benefit--payout{left:27px} .benefit--payout .text{margin-left:28px}
  .benefit--evals{left:190px} .benefit--evals .text{margin-left:27px}
  .benefit--afford{left:353px} .benefit--afford .text{margin-left:28px}
  .benefit--leaders{left:520px} .benefit--leaders .text{margin-left:27px}
  .benefit .text h3{margin-bottom:0}
  .benefit .text p{margin-left:-28px}
  .benefit--evals .text p,.benefit--leaders .text p{margin-left:-27px}
  .divider{position:absolute;top:27px;width:1.5px;height:50px;background:var(--navy)}

  /* Contact bar */
  .contact-label{left:22px;top:417px;color:var(--white);font-weight:700;font-size:13.5px;line-height:17px}
  .contact-label .thin{font-weight:400}
  .contact-phone{left:272px;top:409px;font-size:25px;font-weight:500;line-height:32px;color:var(--navy);letter-spacing:0.3px}
  .contact-web{left:457px;top:417px;font-size:12.4px;font-weight:600;line-height:17px;color:var(--navy)}

  /* Back */
  .refer-stack{position:absolute;left:56px;top:16px;width:170px;transform:scaleX(0.78);transform-origin:left top;text-align:center;font-family:"Anton",sans-serif;line-height:1}
  .refer-stack span{display:block}
  .refer-stack .lead{color:var(--white);font-size:30px;line-height:30px}
  .refer-stack .hero{font-size:70px;line-height:60px;background:linear-gradient(180deg,#f9e23a 0%,#f2b83a 60%,var(--orange) 100%);-webkit-background-clip:text;background-clip:text;color:transparent}
  .refer-stack .hero--earn{font-size:80px;line-height:66px}

  .how-title{left:38px;top:212px;font-weight:700;font-size:16.5px;letter-spacing:4.5px;line-height:22px}
  .how-title .r{color:var(--red)} .how-title .n{color:var(--navy)}

  .step-caption{position:absolute;top:342px;width:193px;color:var(--white);font-family:"Roboto Condensed",sans-serif;font-weight:400;font-size:14px;line-height:18.5px;text-align:center}
  .step-caption--1{left:25px}
  .step-caption--2{left:243px}
  .step-caption--3{left:459px}
</style>
</head>
<body>

<!-- FRONT -->
<section class="card card--front" aria-label="Referral flyer front">
  <svg class="shapes" viewBox="0 0 684 442" aria-hidden="false">
    <defs>
      <radialGradient id="heroBlue" cx="0.45" cy="0.5" r="0.7">
        <stop offset="0" stop-color="#235b93"/>
        <stop offset="1" stop-color="#1a4a7c"/>
      </radialGradient>
      <linearGradient id="skyline" x1="0" y1="0" x2="0" y2="1">
        <stop offset="0" stop-color="#8a6fb0"/>
        <stop offset="0.45" stop-color="#b57a9a"/>
        <stop offset="0.72" stop-color="#a5673f"/>
        <stop offset="1" stop-color="#3a3a5a"/>
      </linearGradient>
    </defs>
    <polygon points="0,0 322,0 280,105 322,223 0,223" fill="url(#heroBlue)"/>
    <g role="img" aria-label="Photo: city skyline at dusk across the bay">
      <polygon points="331,0 684,0 684,223 330,223 289,105" fill="url(#skyline)"/>
    </g>
    <!-- Incentive box -->
    <polygon points="20,292 42,292 30,255" fill="var(--yellow)"/>
    <polygon points="20,229 172,229 194,292 42,292 30,255" fill="var(--red)"/>
    <polygon points="172,229 328,229 349,292 194,292" fill="var(--blue-bright)"/>
    <!-- Premier ribbon -->
    <polygon points="331,229 641,229 650,256 342,256" fill="var(--yellow)"/>
    <polygon points="342,256 500,256 500,293 356,293" fill="var(--red)"/>
    <polygon points="500,256 655,256 663,293 500,293" fill="var(--blue-bright)"/>
    <path d="M500 258 L514 263 L514 277 Q514 289 500 296 Q486 289 486 277 L486 263 Z" fill="var(--yellow)"/>
    <path d="M493 276 L498 282 L508 269" fill="none" stroke="var(--blue-bright)" stroke-width="3.2" stroke-linecap="round" stroke-linejoin="round"/>
    <!-- Contact bar -->
    <polygon points="0,409 249,409 261,442 0,442" fill="var(--navy)"/>
  </svg>

  <h1 class="headline"><span class="earn">EARN</span><span class="unlimited">UNLIMITED</span><span class="cash">CASH</span></h1>

  <div class="abs amount amount--min"><span class="big"><sup>$</sup>500</span><span class="small">MINIMUM</span></div>
  <div class="abs or-box">OR</div>
  <div class="abs amount amount--pct"><span class="big">10%</span><span class="small">PER REFERRAL</span></div>

  <div class="abs ribbon-text ribbon-premier">PREMIER</div>
  <div class="abs ribbon-text ribbon-partner">PARTNER</div>
  <div class="abs ribbon-text ribbon-program">PROGRAM</div>

  <div class="benefits">
    <div class="abs spaced benefits-title"><span class="r">PARTNER WITH US</span> <span class="n">&amp; EVERYBODY WINS!</span></div>

    <div class="benefit benefit--payout">
      <svg class="icon" viewBox="0 0 24 26"><path d="M12 1l3 2.5 4-.5 1 3.8 3 2.7-1.8 3.5 1.8 3.5-3 2.7-1 3.8-4-.5L12 25l-3-2.5-4 .5-1-3.8-3-2.7L2.8 13 1 9.5l3-2.7 1-3.8 4 .5z" fill="var(--navy)"/><text x="12" y="17.5" text-anchor="middle" font-family="Poppins,sans-serif" font-weight="700" font-size="13" fill="#fff">$</text></svg>
      <div class="text"><h3>Guaranteed<br>Payout</h3><p>Minimum $500 or 10%<br>of Total Invoice Paid Fast</p></div>
    </div>
    <div class="divider" style="left:168px"></div>

    <div class="benefit benefit--evals">
      <svg class="icon" viewBox="0 0 24 26"><path d="M4 1h16v19l-4 5H4z" fill="var(--navy)"/><path d="M8 7h8M8 11h8M8 15h8" stroke="#fff" stroke-width="1.8"/></svg>
      <div class="text"><h3>Free<br>Evaluations</h3><p>Fast &amp; Free Inspections<br>and Written Estimates</p></div>
    </div>
    <div class="divider" style="left:328px"></div>

    <div class="benefit benefit--afford">
      <svg class="icon" viewBox="0 0 24 26"><circle cx="12" cy="13" r="11" fill="var(--navy)"/><text x="10" y="18" text-anchor="middle" font-family="Poppins,sans-serif" font-weight="700" font-size="13" fill="#fff">$</text><path d="M17 8v8M15 14l2 2.5 2-2.5" stroke="#fff" stroke-width="1.6" fill="none"/></svg>
      <div class="text"><h3>Affordable<br>Solutions</h3><p>Lowest Out of Pocket<br>Costs for Your Customers</p></div>
    </div>
    <div class="divider" style="left:500px"></div>

    <div class="benefit benefit--leaders">
      <svg class="icon" viewBox="0 0 24 26"><circle cx="10" cy="7" r="5.5" fill="var(--navy)"/><path d="M0 24c0-7 4-10 10-10s10 3 10 10z" fill="var(--navy)"/><circle cx="19" cy="17" r="4.5" fill="var(--navy)" stroke="#fff" stroke-width="1"/><path d="M17 17l1.5 1.5 2.5-3" stroke="#fff" stroke-width="1.3" fill="none"/></svg>
      <div class="text"><h3>Industry<br>Leaders</h3><p>Licensed &amp; Certified Experts<br>Provide 100% Guarantee</p></div>
    </div>

    <div class="abs spaced benefits-footer"><span class="n">SEND</span> <span class="r">REFERRALS.</span> <span class="n">GET</span> <span class="r">PAID.</span> <span class="n">GROW</span> <span class="r">YOUR BUSINESS</span></div>
  </div>

  <div class="abs contact-label">CALL, TEXT <span class="thin">OR</span> BOOK ONLINE</div>
  <div class="abs contact-phone">858-471-6093</div>
  <div class="abs contact-web">WWW.BRIGHTLANERENOVATE.COM</div>
</section>

<!-- BACK -->
<section class="card card--back" aria-label="Referral flyer back">
  <svg class="shapes" viewBox="0 0 684 442">
    <defs>
      <linearGradient id="bills" x1="0" y1="0" x2="1" y2="1">
        <stop offset="0" stop-color="#d7dad4"/>
        <stop offset="0.5" stop-color="#b9d4e0"/>
        <stop offset="1" stop-color="#c6c9c2"/>
      </linearGradient>
      <linearGradient id="flood" x1="0" y1="0" x2="0" y2="1">
        <stop offset="0" stop-color="#cfc6bd"/><stop offset="1" stop-color="#4f9cc4"/>
      </linearGradient>
      <linearGradient id="estimate" x1="0" y1="0" x2="0" y2="1">
        <stop offset="0" stop-color="#d9dde2"/><stop offset="1" stop-color="#6d8a55"/>
      </linearGradient>
      <linearGradient id="sky" x1="0" y1="0" x2="0" y2="1">
        <stop offset="0" stop-color="#2f6fb4"/><stop offset="1" stop-color="#bcd8ee"/>
      </linearGradient>
    </defs>
    <rect x="0" y="0" width="684" height="206" fill="var(--blue)"/>
    <polygon points="0,206 0,128 54,18 186,18 170,206" fill="var(--navy-deep)"/>
    <polygon points="194,0 323,0 258,108" fill="var(--red)"/>
    <g role="img" aria-label="Photo: scattered dollar bills with blue letter tiles spelling CASH FLOW">
      <polygon points="323,0 684,0 684,206 194,206" fill="url(#bills)"/>
    </g>
    <!-- How it works band -->
    <polygon points="0,206 251,206 238,239 0,239" fill="var(--yellow)"/>
    <g fill="var(--yellow)">
      <polygon points="273,206 294,206 281,222 260,222"/>
      <polygon points="309,206 330,206 317,222 296,222"/>
      <polygon points="345,206 366,206 353,222 332,222"/>
      <polygon points="381,206 402,206 389,222 368,222"/>
      <polygon points="417,206 438,206 425,222 404,222"/>
      <polygon points="453,206 474,206 461,222 440,222"/>
      <polygon points="489,206 510,206 497,222 476,222"/>
      <polygon points="525,206 546,206 533,222 512,222"/>
      <polygon points="561,206 582,206 569,222 548,222"/>
      <polygon points="597,206 618,206 605,222 584,222"/>
      <polygon points="633,206 654,206 641,222 620,222"/>
      <polygon points="669,206 684,206 684,222 656,222"/>
    </g>
    <!-- Step images -->
    <g role="img" aria-label="Photo: air movers drying a flooded room"><rect x="25" y="256" width="193" height="84" fill="url(#flood)"/></g>
    <g role="img" aria-label="Photo: inspector with a tablet in front of a house"><rect x="243" y="256" width="193" height="84" fill="url(#estimate)"/></g>
    <g role="img" aria-label="Photo: yellow road sign reading Get Paid to Share against a blue sky"><rect x="459" y="256" width="193" height="84" fill="url(#sky)"/></g>
    <!-- Step captions -->
    <polygon points="25,340 218,340 218,377 206,389 25,389" fill="var(--navy)"/>
    <polygon points="243,340 436,340 436,377 424,389 232,389" fill="var(--navy)"/>
    <polygon points="459,340 652,340 652,377 640,389 448,389" fill="var(--navy)"/>
    <!-- Contact bar -->
    <polygon points="0,409 249,409 261,442 0,442" fill="var(--navy)"/>
  </svg>

  <h2 class="refer-stack">
    <span class="lead">THE MORE YOU</span>
    <span class="hero">REFER</span>
    <span class="lead">THE MORE YOU</span>
    <span class="hero hero--earn">EARN</span>
  </h2>

  <div class="abs how-title"><span class="r">HOW</span> <span class="n">IT WORKS</span></div>

  <p class="step-caption step-caption--1">Refer Flood, Mold &amp;<br>Construction Jobs</p>
  <p class="step-caption step-caption--2">We Schedule a Free Estimate.<br>If Approved, You Get Paid.</p>
  <p class="step-caption step-caption--3">Everybody Benefits<br>From Referrals</p>

  <div class="abs contact-label">CALL, TEXT <span class="thin">OR</span> BOOK ONLINE</div>
  <div class="abs contact-phone">858-471-6093</div>
  <div class="abs contact-web">WWW.BRIGHTLANERENOVATE.COM</div>
</section>

</body>
</html>
```